Rollers & Glides.com

Vertical Business Card with focus on branding with our icon. Information on card will be logo, persons name, position, phone number, email address and website. Use the the name Marcus Pellow, position President, phone number 480.915.2267, email Marcus@rollersandglides-demo.com, website www.rollersandglides-demo.com.

```html
<!DOCTYPE html>
<html lang="en">
<head>
<meta charset="utf-8">
<title>Rollers &amp; Glides.com – Business Card</title>
<link rel="stylesheet" href="https://fonts.googleapis.com/css2?family=Roboto:wght@400;700&display=swap">
<style>
  :root {
    --brand-blue: #325fab;
    --backdrop: #b9b9b9;
    --paper: #ffffff;
    --ink: #1e1e1e;
    --card-shadow: #1a1a1a;
  }
  * { margin: 0; padding: 0; box-sizing: border-box; }
  html, body {
    width: 1200px;
    height: 801px;
    overflow: hidden;
    background: var(--backdrop);
    font-family: "Roboto", Arial, sans-serif;
  }
  .canvas {
    position: relative;
    width: 1200px;
    height: 801px;
  }
  .card {
    position: absolute;
    top: 274px;
    width: 443px;
    height: 263px;
    box-shadow: 3px 3px 0 var(--card-shadow);
    overflow: hidden;
  }
  .card--front { left: 153px; background: var(--paper); }
  .card--back { left: 625px; background: var(--brand-blue); }

  .front__band {
    position: absolute;
    left: 0; top: 0;
    width: 61px; height: 100%;
    background: var(--brand-blue);
  }
  .brand-mark {
    position: absolute;
    border-radius: 50%;
  }
  .card--front .brand-mark {
    left: 302px; top: 38px;
    width: 56px; height: 56px;
    background: var(--brand-blue);
  }
  .card--back .brand-mark {
    left: 186px; top: 76px;
    width: 70px; height: 70px;
    background: var(--paper);
  }
  .brand-name {
    position: absolute;
    font-weight: 400;
    white-space: nowrap;
    letter-spacing: 0.3px;
  }
  .card--front .brand-name {
    right: 22px; top: 106px;
    font-size: 20px;
    color: var(--brand-blue);
  }
  .card--back .brand-name {
    left: 0; right: 0; top: 164px;
    text-align: center;
    font-size: 25px;
    color: var(--paper);
  }

  .person {
    position: absolute;
    left: 84px; top: 143px;
  }
  .person__name {
    font-size: 16px;
    font-weight: 700;
    color: var(--brand-blue);
    text-transform: uppercase;
    line-height: 18px;
  }
  .person__role {
    font-size: 12.5px;
    color: var(--ink);
    line-height: 15px;
  }
  .contact-list {
    position: absolute;
    left: 84px; top: 192px;
    list-style: none;
  }
  .contact-list__item {
    display: flex;
    align-items: center;
    gap: 5px;
    font-size: 12.5px;
    color: var(--ink);
    line-height: 16px;
  }
  .contact-list__icon {
    width: 11px; height: 11px;
    flex: none;
  }
  .contact-list__domain { color: var(--brand-blue); }
</style>
</head>
<body>
<div class="canvas">
  <section class="card card--front" aria-label="Business card front">
    <div class="front__band"></div>
    <span class="brand-mark"></span>
    <p class="brand-name">Rollers &amp; Glides.com</p>
    <div class="person">
      <h1 class="person__name">Marcus Pellow</h1>
      <p class="person__role">President</p>
    </div>
    <ul class="contact-list">
      <li class="contact-list__item">
        <svg class="contact-list__icon" viewBox="0 0 24 24" aria-hidden="true"><path fill="#325fab" d="M6.6 10.8a15.1 15.1 0 0 0 6.6 6.6l2.2-2.2c.3-.3.7-.4 1-.2 1.1.4 2.3.6 3.6.6.6 0 1 .4 1 1V20c0 .6-.4 1-1 1A17 17 0 0 1 3 4c0-.6.4-1 1-1h3.5c.6 0 1 .4 1 1 0 1.3.2 2.5.6 3.6.1.3 0 .7-.2 1z"/></svg>
        <span>480.915.2267</span>
      </li>
      <li class="contact-list__item">
        <svg class="contact-list__icon" viewBox="0 0 24 24" aria-hidden="true"><rect x="1" y="5" width="22" height="14" fill="#325fab"/><path d="M1 5l11 8 11-8" fill="none" stroke="#fff" stroke-width="1.6"/></svg>
        <span>Marcus@rollersandglides-demo.com</span>
      </li>
      <li class="contact-list__item">
        <svg class="contact-list__icon" viewBox="0 0 24 24" aria-hidden="true"><g fill="none" stroke="#325fab" stroke-width="2"><circle cx="12" cy="12" r="10"/><ellipse cx="12" cy="12" rx="4.5" ry="10"/><path d="M2 12h20M4 7h16M4 17h16"/></g></svg>
        <span>www.<span class="contact-list__domain">rollersandglides-demo</span>.com</span>
      </li>
    </ul>
  </section>

  <section class="card card--back" aria-label="Business card back">
    <span class="brand-mark"></span>
    <p class="brand-name">Rollers &amp; Glides.com</p>
  </section>
</div>
</body>
</html>
```